(removed) area Multi-store hair salon needs a poster for a special service

We need a poster for a soon to be multi-store hair salon based in the (removed) area. We are expanding, opening more salons. We need a poster for a service we offer called "The Fullset!" It is for men, and it includes:
1. Haircut
2. Shampoo
3. Neck Shave
4. Hot Towel Service

We charge $22 for The Fullset!
70% of our clients are men.
Our website is www.trimvane.example
Our colors are black and red
***Please focus on the "The Fullset!" part of the poster. We are almost looking for logo or icon for The Fullset! part. *****
This will be hung inside the store near the reception area and possibly through out the salon and could be included in emails.
I have attached our logo and some other branding items we use (business cards, rewards cards, envelopes, etc) to help give you an idea of the look and feel we currently have. I have also attached an ad from Pelham which is a coupon they use for a service they call the fullset, just to give an idea. We like how Pelham created "The Fullset" as an icon or logo.

Target Market(s)

Men

Industry/Entity Type

Store

Requirements
Nice to have
• Pictures of each service. We uploaded some examples.
• Also, "The Fullset!" should be like a logo/icon

```html
<!DOCTYPE html>
<html lang="en">
<head>
<meta charset="utf-8">
<title>Get The Fullset! For Men – Trimvane</title>
<link rel="stylesheet" href="https://fonts.googleapis.com/css2?family=Bowlby+One&family=Anton&family=Archivo+Black&family=Arimo:wght@700&display=swap">
<style>
  :root {
    --red: #d0202a;
    --black: #111111;
    --white: #ffffff;
    --grey: #9a9a9a;
    --tick: #d42a2f;
  }
  * { box-sizing: border-box; margin: 0; padding: 0; }
  html, body { width: 900px; height: 1200px; overflow: hidden; background: var(--white); }
  .poster { position: relative; width: 900px; height: 1200px; overflow: hidden; background: var(--white); }
  .backdrop { position: absolute; inset: 0; }
  .headline-art { position: absolute; inset: 0; }
  .headline-art text { font-family: "Bowlby One", "Archivo Black", sans-serif; }

  .brand-lockup {
    position: absolute; left: 385px; top: 168px;
    display: flex; align-items: center; gap: 12px;
  }
  .brand-dot { width: 46px; height: 46px; border-radius: 50%; background: var(--black); }
  .brand-name {
    font-family: "Archivo Black", sans-serif; font-size: 36px; color: var(--black);
    letter-spacing: 1px; line-height: 1;
  }

  .service-photo {
    position: absolute; left: 103px; width: 188px; height: 188px;
    border: 3px solid var(--white); box-shadow: 0 0 0 1px rgba(0,0,0,.25);
  }
  .photo-shampoo { top: 385px; background: linear-gradient(135deg, #3a3634, #cdb79a 45%, #e9e1d6 60%, #2a2a2a); }
  .photo-haircut { top: 586px; background: linear-gradient(160deg, #1d1a18, #c99b76 40%, #d8b27a 70%, #a57a45); }
  .photo-towel   { top: 786px; background: linear-gradient(180deg, #3b3936, #b48c63 35%, #c9a27a 65%, #2d2b29); }
  .photo-shave   { top: 986px; background: linear-gradient(150deg, #b08d6a, #d9b894 45%, #efe7dc 70%, #c29a72); }

  .for-men {
    position: absolute; left: 487px; top: 380px;
    font-family: "Bowlby One", sans-serif; font-size: 62px; color: var(--red);
    letter-spacing: 1px; line-height: 1;
    text-shadow: 0 0 2px #fff, 2px 3px 4px rgba(0,0,0,.45);
  }
  .you-get {
    position: absolute; left: 478px; top: 530px;
    font-family: "Bowlby One", sans-serif; font-size: 46px; color: var(--red); line-height: 1;
  }
  .service-list { position: absolute; left: 343px; top: 588px; list-style: none; }
  .service-item {
    display: flex; align-items: center; height: 61px;
    font-family: "Arimo", Arial, sans-serif; font-weight: 700; font-size: 48px; color: var(--black);
  }
  .check { width: 52px; height: 52px; margin-right: 2px; flex: none; }

  .price-badge {
    position: absolute; left: 434px; top: 867px; width: 328px; height: 328px;
    border-radius: 50%; background: var(--red);
    color: var(--white); font-family: "Anton", sans-serif;
    text-shadow: 2px 3px 4px rgba(0,0,0,.45);
  }
  .price-lead { position: absolute; left: 48px; top: 58px; font-size: 50px; line-height: 50px; }
  .price-amount { position: absolute; left: 46px; top: 166px; font-size: 130px; line-height: 1; display: flex; }
  .price-amount .currency { font-size: 54px; margin-top: 6px; }
  .price-amount .cents { font-size: 54px; margin-top: 10px; margin-left: 4px; }
</style>
</head>
<body>
<main class="poster">
  <svg class="backdrop" width="900" height="1200" viewBox="0 0 900 1200" aria-hidden="true">
    <rect width="900" height="1200" fill="var(--red)"/>
    <path d="M430,0 C60,230 70,900 440,1200" fill="none" stroke="var(--grey)" stroke-width="16"/>
    <path d="M405,0 C40,240 60,900 420,1200 L900,1200 L900,0 Z" fill="var(--white)"/>
    <path d="M250,1030 C300,1110 350,1160 410,1200" fill="none" stroke="var(--black)" stroke-width="10"/>
  </svg>

  <svg class="headline-art" width="900" height="1200" viewBox="0 0 900 1200">
    <text x="30" y="113" font-size="100" fill="var(--white)" textLength="270" lengthAdjust="spacingAndGlyphs">GET</text>
    <text x="150" y="230" font-size="118" fill="var(--black)" textLength="195" lengthAdjust="spacingAndGlyphs">THE</text>
    <text x="195" y="362" font-size="148" fill="var(--red)" stroke="var(--black)" stroke-width="10"
          paint-order="stroke" stroke-linejoin="round" textLength="685" lengthAdjust="spacingAndGlyphs">FULLSET!</text>
  </svg>

  <div class="brand-lockup">
    <span class="brand-dot"></span>
    <span class="brand-name">TRIMVANE</span>
  </div>

  <div class="service-photo photo-shampoo" role="img" aria-label="Photo: client receiving a shampoo at the wash basin"></div>
  <div class="service-photo photo-haircut" role="img" aria-label="Photo: barber cutting hair with scissors and comb"></div>
  <div class="service-photo photo-towel" role="img" aria-label="Photo: hot towel wrapped over client's face"></div>
  <div class="service-photo photo-shave" role="img" aria-label="Photo: neck shave with straight razor"></div>

  <div class="for-men">FOR MEN</div>
  <div class="you-get">YOU GET:</div>

  <ul class="service-list">
    <li class="service-item"><svg class="check" viewBox="0 0 52 52" aria-hidden="true"><rect x="4" y="22" width="24" height="24" fill="none" stroke="var(--black)" stroke-width="3"/><path d="M6,28 L16,40 L44,6" fill="none" stroke="var(--tick)" stroke-width="7" stroke-linecap="round"/></svg>Shampoo</li>
    <li class="service-item"><svg class="check" viewBox="0 0 52 52" aria-hidden="true"><rect x="4" y="22" width="24" height="24" fill="none" stroke="var(--black)" stroke-width="3"/><path d="M6,28 L16,40 L44,6" fill="none" stroke="var(--tick)" stroke-width="7" stroke-linecap="round"/></svg>Haircut</li>
    <li class="service-item"><svg class="check" viewBox="0 0 52 52" aria-hidden="true"><rect x="4" y="22" width="24" height="24" fill="none" stroke="var(--black)" stroke-width="3"/><path d="M6,28 L16,40 L44,6" fill="none" stroke="var(--tick)" stroke-width="7" stroke-linecap="round"/></svg>Hot Towel Service</li>
    <li class="service-item"><svg class="check" viewBox="0 0 52 52" aria-hidden="true"><rect x="4" y="22" width="24" height="24" fill="none" stroke="var(--black)" stroke-width="3"/><path d="M6,28 L16,40 L44,6" fill="none" stroke="var(--tick)" stroke-width="7" stroke-linecap="round"/></svg>Neck Shave</li>
  </ul>

  <div class="price-badge">
    <div class="price-lead">ALL FOR<br>ONLY</div>
    <div class="price-amount"><span class="currency">$</span>22<span class="cents">00</span></div>
  </div>
</main>
</body>
</html>
```